Images and design ideas provided: Postcard size flier

2 sided postcard size flier to hand people on the street.

A FUN tax business needs a postcard size flier to hand people on the street. Not a typical serious, quiet, office so make the image fun!

Exact wording, logo and key images provided. You are free to add other images as you see fit (such as money).

Side 1: Use image of lady looking up (she should be looking at text provided).All spanish and english text provided. Logo in bottom right corner. Address at bottom of card.

Side 2: Image of lady holding money and pointing. Remove money and have her holding a sign/or some other creative way to have her looking at text. All spanish and english text provided. Logo in bottom right corner. Address at bottom of card.

Size: 4" x 6" horizontal or vertical is ok
Each side can be different and image/design does not have to be related.

Target Market(s)

Age 18-35

Industry/Entity Type

Accounting

Font styles to use
Sans Serif

Colors

Designer to choose colors to be used in the design.

Requirements
Must have
• Use text document provided. All text goes on both sides.
• Should be easy to read from a few feet away.
Nice to have
• Bright colors to attract attention of people walking by to grab flier/card. Images of money ok.
Should not have
• No images of calculators or typical accounting tax forms.

```html
<!DOCTYPE html>
<html lang="en">
<head>
<meta charset="utf-8">
<title>Refund Royale – Postcard Flier</title>
<link rel="stylesheet" href="https://fonts.googleapis.com/css2?family=Anton&family=Open+Sans:wght@400;600;700;800&display=swap">
<style>
  :root {
    --stage: #e9e4dc;
    --red: #d8101c;
    --blue: #0b3f9a;
    --ink: #1b1b1b;
    --white: #ffffff;
    --label: #4a4a4a;
    --footer-top: #f1f1f1;
    --footer-bottom: #cfd3d8;
  }
  * { margin: 0; padding: 0; box-sizing: border-box; }
  html, body { width: 1200px; height: 1003px; overflow: hidden; }
  body { background: var(--stage); position: relative; font-family: "Open Sans", sans-serif; }

  .card {
    position: absolute; top: 126px; width: 491px; height: 736px; overflow: hidden;
    background: linear-gradient(180deg, #cfe2df 0%, #a8cdd2 22%, #6fa6cf 45%, #2f6ab8 70%, #1646a0 100%);
    box-shadow: 0 4px 14px rgba(0,0,0,.25);
  }
  .card--front { left: 86px; }
  .card--back { left: 623px; }

  .money-texture {
    position: absolute; left: 0; top: 0; width: 491px; height: 330px;
    background: linear-gradient(180deg, rgba(160,190,180,.55), rgba(160,190,180,0));
  }

  .headline { position: absolute; left: 0; width: 100%; text-align: center; }
  .headline--get {
    top: 36px; font-family: "Anton", sans-serif; font-size: 98px; line-height: 1;
    color: var(--red); letter-spacing: 1px; text-shadow: 0 2px 0 rgba(255,255,255,.6);
  }
  .headline--cash {
    top: 128px; font-family: "Open Sans", sans-serif; font-weight: 800; font-size: 63px;
    line-height: 1; color: var(--blue); letter-spacing: -1px; text-shadow: 0 2px 0 rgba(255,255,255,.6);
  }
  .subline { position: absolute; left: 0; width: 100%; text-align: center; font-weight: 700; }
  .subline--en { top: 210px; font-size: 24.5px; color: var(--ink); }
  .subline--es { top: 240px; font-size: 20.5px; color: var(--white); }
  .subline--es-small { top: 265px; font-size: 14px; font-weight: 600; color: var(--ink); }

  .flag-art {
    position: absolute; left: 0; top: 338px; width: 491px; height: 240px;
    background: linear-gradient(170deg, rgba(40,80,170,.0) 0%, rgba(60,100,190,.8) 35%, rgba(200,120,140,.55) 60%, rgba(230,235,245,.6) 75%, rgba(30,70,160,.3) 100%);
  }
  .person-photo { position: absolute; top: 306px; height: 384px; }
  .card--front .person-photo {
    left: 130px; width: 361px;
    background: linear-gradient(180deg, #c9a94a 0%, #b7b38a 25%, #8f9a6b 60%, #7a7f52 100%);
    border-radius: 140px 140px 0 0;
  }
  .card--back .person-photo {
    left: 13px; width: 308px;
    background: linear-gradient(180deg, #c8424a 0%, #c9a94a 25%, #8f9a6b 60%, #7a7f52 100%);
    border-radius: 120px 120px 0 0;
  }

  .brand-name {
    position: absolute; top: 630px; color: var(--white);
    font-family: "Open Sans", sans-serif; font-weight: 800; font-size: 21px;
    line-height: 1.05; text-transform: uppercase; letter-spacing: .5px;
  }
  .card--front .brand-name { left: 26px; }
  .card--back .brand-name { right: 26px; text-align: left; }

  .contact-bar {
    position: absolute; left: 0; bottom: 0; width: 100%; height: 46px;
    border-top: 2px solid var(--red);
    background: linear-gradient(180deg, var(--footer-top), var(--footer-bottom));
    display: flex; align-items: center; justify-content: center; gap: 7px;
  }
  .contact-bar__pin { width: 17px; height: 17px; }
  .contact-bar__address { font-size: 11.5px; font-weight: 700; color: #8a1a2a; }
  .contact-bar__divider { width: 1px; height: 20px; background: #8a8a8a; margin: 0 3px; }
  .contact-bar__call { font-size: 15px; color: #6b6b6b; }
  .contact-bar__phone { font-size: 21px; font-weight: 700; color: var(--blue); }

  .side-label { position: absolute; font-size: 36px; color: var(--label); }
  .side-label--front { left: 262px; top: 882px; }
  .side-label--back { left: 824px; top: 896px; }
</style>
</head>
<body>

<section class="card card--front">
  <div class="money-texture" role="img" aria-label="Background of scattered dollar bills"></div>
  <div class="headline headline--get">GET $100</div>
  <div class="headline headline--cash">CASH NOW!</div>
  <div class="subline subline--en">WITH PAID TAX PREPARATION</div>
  <div class="subline subline--es">RECIBA $100 EN EFECTIVO AHORA!</div>
  <div class="subline subline--es-small">CON LA PREPARACION PAGADA DE SUS IMPUESTOS</div>
  <div class="flag-art" role="img" aria-label="Waving American flag illustration"></div>
  <div class="person-photo" role="img" aria-label="Photo of a woman in a royal costume and crown looking up at the headline with arms raised"></div>
  <div class="brand-name">Refund<br>Royale</div>
  <div class="contact-bar">
    <svg class="contact-bar__pin" viewBox="0 0 20 20"><circle cx="10" cy="10" r="9" fill="none" stroke="#d8101c" stroke-width="1.6"/><path d="M10 4.5a3.5 3.5 0 0 0-3.5 3.5c0 2.6 3.5 6.5 3.5 6.5s3.5-3.9 3.5-6.5A3.5 3.5 0 0 0 10 4.5z" fill="#0b3f9a"/><circle cx="10" cy="8" r="1.3" fill="#fff"/></svg>
    <span class="contact-bar__address">418 Maple Ave. Bronx NY 10455</span>
    <span class="contact-bar__divider"></span>
    <span class="contact-bar__call">Call Us:</span>
    <span class="contact-bar__phone">(718) 555-0147</span>
  </div>
</section>

<section class="card card--back">
  <div class="money-texture" role="img" aria-label="Background of scattered dollar bills"></div>
  <div class="headline headline--get">GET $100</div>
  <div class="headline headline--cash">CASH NOW!</div>
  <div class="subline subline--en">WITH PAID TAX PREPARATION</div>
  <div class="subline subline--es">RECIBA $100 EN EFECTIVO AHORA!</div>
  <div class="subline subline--es-small">CON LA PREPARACION PAGADA DE SUS IMPUESTOS</div>
  <div class="flag-art" role="img" aria-label="Waving American flag illustration"></div>
  <div class="person-photo" role="img" aria-label="Photo of a woman in a royal costume and crown holding cash and pointing toward it"></div>
  <div class="brand-name">Refund<br>Royale</div>
  <div class="contact-bar">
    <svg class="contact-bar__pin" viewBox="0 0 20 20"><circle cx="10" cy="10" r="9" fill="none" stroke="#d8101c" stroke-width="1.6"/><path d="M10 4.5a3.5 3.5 0 0 0-3.5 3.5c0 2.6 3.5 6.5 3.5 6.5s3.5-3.9 3.5-6.5A3.5 3.5 0 0 0 10 4.5z" fill="#0b3f9a"/><circle cx="10" cy="8" r="1.3" fill="#fff"/></svg>
    <span class="contact-bar__address">418 Maple Ave. Bronx NY 10455</span>
    <span class="contact-bar__divider"></span>
    <span class="contact-bar__call">Call Us:</span>
    <span class="contact-bar__phone">(718) 555-0147</span>
  </div>
</section>

<div class="side-label side-label--front">Front</div>
<div class="side-label side-label--back">Back</div>

</body>
</html>
```